New Fun, Positive, energised looking Business Card Needed for High Achiever Coach

I am looking for a two sided full colour business card. I am self employed and have recently re branded my 1-2-1 work re-vitalising high achievers. My target client base for these cards is therefore high achievers - usually aged 40 -55, they are often entrepreneurs, CEO or work in banking and finance and 2/3 are male. I work with them on 90 day or 6 month coaching programs to help them live their success in a healthier, more sustainable and fulfiiled way. They pay for this privately so though they are corporate types the cards need not look 'corporate'. I want to portray the idea of transformation, vitality and re-connecting.
You can get a feel for the look I like on my new website: morvenlisk.co.uk
I want to use this logo with strapline (Re-Vitalising High Achievers) (I purchased off Logoharbor) and font/ colours (the turquoise and green).
Details to include on the card:
www.morvenlisk.co.uk
+44 7915 302618
morven@morvenlisk.co.uk
skype: morvenlisk
I'd also like to include:
Do you struggle to switch off? Want to be healthier and feel fitter? Want closer relationships? More clarity over the direction you are headed? I can help you do these things using integrated mind-body techniques. Visit morvenlisk.co.uk TODAY to apply for a FREE Breakthrough session.
BUT if that is too much text for a card I am open to advice/ammendments.
Updates
Thanks for your design - I am considering them. PLease change the wording to :

```html
<!DOCTYPE html>
<html lang="en">
<head>
<meta charset="utf-8">
<title>Morven Lisk – Business Card</title>
<link href="https://fonts.googleapis.com/css2?family=Source+Sans+3:wght@400;600;700&display=swap" rel="stylesheet">
<style>
  :root {
    --green: #5dbd6c;
    --turquoise: #15a4c9;
    --brand-blue: #1b9dc6;
    --white: #ffffff;
    --backdrop: #ecefef;
    --card-shadow: rgba(0, 0, 0, 0.18);
  }
  * { box-sizing: border-box; margin: 0; padding: 0; }
  html, body {
    width: 1200px;
    height: 720px;
    overflow: hidden;
  }
  body {
    background: var(--backdrop);
    font-family: "Source Sans 3", Arial, sans-serif;
    color: var(--white);
    display: flex;
    align-items: center;
    justify-content: center;
    gap: 60px;
  }
  .card {
    position: relative;
    width: 525px;
    height: 300px;
    border-radius: 4px;
    overflow: hidden;
    box-shadow: 0 6px 18px var(--card-shadow);
    display: flex;
    flex-direction: column;
  }

  /* Front */
  .front-identity {
    height: 150px;
    background: var(--white);
    display: flex;
    flex-direction: column;
    align-items: center;
    justify-content: center;
    gap: 4px;
  }
  .brand-name {
    font-weight: 700;
    font-size: 38px;
    color: var(--brand-blue);
    letter-spacing: 0.5px;
    line-height: 1;
  }
  .strapline {
    font-weight: 400;
    font-size: 15px;
    color: var(--brand-blue);
    letter-spacing: 0.3px;
  }
  .web-band {
    height: 42px;
    background: var(--green);
    display: flex;
    align-items: center;
    justify-content: center;
    font-size: 17px;
    letter-spacing: 3px;
    border-bottom: 3px solid var(--white);
  }
  .contact-panel {
    flex: 1;
    background: var(--turquoise);
    display: flex;
    flex-direction: column;
    align-items: center;
    justify-content: center;
    gap: 8px;
    font-size: 15px;
  }
  .contact-row {
    display: flex;
    gap: 22px;
    align-items: center;
  }
  .contact-item {
    display: flex;
    align-items: center;
    gap: 6px;
  }
  .contact-item svg { width: 14px; height: 14px; flex: none; }

  /* Back */
  .questions {
    height: 158px;
    background: var(--green);
    display: flex;
    flex-direction: column;
    align-items: center;
    justify-content: center;
    text-align: center;
    font-size: 18px;
    line-height: 1.3;
  }
  .offer {
    position: relative;
    flex: 1;
    background: var(--turquoise);
    display: flex;
    flex-direction: column;
    align-items: center;
    justify-content: center;
    text-align: center;
    font-size: 18px;
    line-height: 1.3;
    gap: 6px;
  }
  .offer strong { font-weight: 700; }
  .faint-brand {
    position: absolute;
    right: 14px;
    top: -40px;
    font-weight: 700;
    font-size: 26px;
    color: var(--white);
    opacity: 0.12;
  }
</style>
</head>
<body>

  <section class="card card-front">
    <div class="front-identity">
      <div class="brand-name">Morven Lisk</div>
      <div class="strapline">Re-Vitalising High Achievers</div>
    </div>
    <div class="web-band">www.morvenlisk.co.uk</div>
    <div class="contact-panel">
      <div class="contact-row">
        <span class="contact-item">
          <svg viewBox="0 0 16 16" aria-hidden="true"><circle cx="8" cy="8" r="7.5" fill="#fff"/><path d="M5.2 3.8c.4-.3.9-.2 1.1.2l.8 1.5c.2.4.1.8-.2 1l-.6.5c.4.9 1.2 1.8 2.2 2.3l.5-.6c.3-.3.7-.4 1-.2l1.5.8c.4.2.5.7.2 1.1l-.6.8c-.4.5-1.1.6-1.7.4C7 10.8 5.2 9 4.4 6.6c-.2-.6 0-1.3.4-1.7z" fill="var(--turquoise)"/></svg>
          +44 7915 302618
        </span>
        <span class="contact-item">
          <svg viewBox="0 0 16 16" aria-hidden="true"><circle cx="8" cy="8" r="7.5" fill="#fff"/><rect x="4" y="5.2" width="8" height="5.6" rx="0.6" fill="var(--turquoise)"/><path d="M4.3 5.6 8 8.4l3.7-2.8" stroke="#fff" stroke-width="0.9" fill="none"/></svg>
          morven@morvenlisk.co.uk
        </span>
      </div>
      <div class="contact-row">
        <span class="contact-item">
          <svg viewBox="0 0 16 16" aria-hidden="true"><circle cx="8" cy="8" r="7.5" fill="#fff"/></svg>
          morvenlisk
        </span>
      </div>
    </div>
  </section>

  <section class="card card-back">
    <div class="questions">
      <p>Do you struggle to switch off?</p>
      <p>Want to be healthier and feel fitter?</p>
      <p>Want closer relationships?</p>
      <p>More clarity over the direction you are headed?</p>
    </div>
    <div class="offer">
      <span class="faint-brand">Morven Lisk</span>
      <p>I can help you do these things using integrated<br>mind-body techniques.</p>
      <p>Visit <strong>morvenlisk.co.uk</strong> TODAY to apply for a<br>FREE Breakthrough session.</p>
    </div>
  </section>

</body>
</html>
```